Mechanical Engineering Business needs a Label Design for Bottle.

We need a Label design for 2 Bottle Sizes of Cutting Paste. This is used for Machine Work Shops big and small to do applications for different cutting processes. Example : Tapping / Broaching / Drilling / Reaming / Knurling / etc. An example of a similar product can be found at https://brimvale-gel.example/product/16-oz-brimvale-gel-bottle/ ... https://brimvale-gel.example/product/2-oz-brimvale-gel-bottle/ ... Our product will be named Orvin - Glide or Orvinex - Glide with our Company logo attached. Currently, we are open to ideas and do not have any fixed concept.

```html
<!DOCTYPE html>
<html lang="en">
<head>
<meta charset="utf-8">
<title>Machining Lubricant – Bottle Label</title>
<link rel="stylesheet" href="https://fonts.googleapis.com/css2?family=Oswald:wght@400;500;600;700&display=swap">
<style>
  :root {
    --page-bg: #f4f4f5;
    --label-white: #ffffff;
    --label-mist: #e4dfe1;
    --maroon: #8c2447;
    --maroon-deep: #6e1a37;
    --maroon-soft: #c25a7e;
    --band-dark: #2b0f18;
    --band-edge: #c7c0c3;
    --title-ink: #4e3139;
    --feature-ink: #ffffff;
    --rule: rgba(255, 255, 255, 0.45);
    --seal-silver: #c9c9cc;
    --seal-rim: #8f8f94;
  }

  * { box-sizing: border-box; margin: 0; padding: 0; }

  html, body {
    width: 1098px;
    height: 1200px;
    overflow: hidden;
    background: var(--page-bg);
    font-family: "Oswald", "Arial Narrow", sans-serif;
  }

  .label {
    position: absolute;
    left: 323px;
    top: 20px;
    width: 452px;
    height: 1160px;
    overflow: hidden;
    background: var(--label-white);
    box-shadow: 0 6px 24px rgba(0, 0, 0, 0.12);
  }

  .label__backdrop {
    position: absolute;
    inset: 0;
    width: 452px;
    height: 1160px;
  }

  .brand {
    position: absolute;
    top: 180px;
    left: 0;
    width: 452px;
    display: flex;
    justify-content: center;
    align-items: center;
    gap: 14px;
  }

  .brand__dot {
    width: 34px;
    height: 34px;
    border-radius: 50%;
    background: var(--maroon);
  }

  .brand__name {
    font-weight: 500;
    font-size: 54px;
    line-height: 1;
    letter-spacing: -1px;
    color: var(--maroon);
    text-transform: uppercase;
  }

  .product-title {
    position: absolute;
    top: 300px;
    left: 0;
    width: 452px;
    text-align: center;
    font-weight: 700;
    font-size: 78px;
    line-height: 80px;
    letter-spacing: -1px;
    color: var(--title-ink);
    text-transform: uppercase;
  }

  .features {
    position: absolute;
    top: 628px;
    left: 66px;
    width: 300px;
    list-style: none;
  }

  .feature {
    display: flex;
    align-items: center;
    gap: 14px;
    color: var(--feature-ink);
    text-transform: uppercase;
    font-weight: 600;
    font-size: 27px;
    line-height: 1.1;
    letter-spacing: -0.3px;
  }

  .feature__icon {
    flex: 0 0 40px;
    width: 40px;
    height: 40px;
  }

  .feature--grade { height: 40px; }
  .feature--thick { height: 40px; margin-top: 38px; }
  .feature--life { margin-top: 40px; align-items: flex-start; }
  .feature--life .feature__icon { margin-top: 14px; }

  .feature__stack { display: flex; flex-direction: column; }
  .feature__stack .lead { font-size: 30px; line-height: 36px; }
  .feature__stack .big { font-size: 38px; line-height: 40px; font-weight: 700; }
  .feature__stack .tail { font-size: 29px; line-height: 36px; font-weight: 500; }

  .feature-rule {
    position: absolute;
    left: 66px;
    width: 282px;
    height: 1px;
    background: linear-gradient(90deg, var(--rule), rgba(255,255,255,0.1));
  }
  .rule-one { top: 687px; }
  .rule-two { top: 765px; }

  .net-content {
    position: absolute;
    left: 49px;
    top: 990px;
    color: var(--feature-ink);
    font-weight: 500;
    font-size: 23px;
    line-height: 30px;
  }

  .guarantee-seal {
    position: absolute;
    left: 222px;
    top: 897px;
    width: 196px;
    height: 196px;
  }
</style>
</head>
<body>
  <main class="label">
    <svg class="label__backdrop" viewBox="0 0 452 1160">
      <defs>
        <linearGradient id="lowerFill" x1="0" y1="0" x2="1" y2="0">
          <stop offset="0" stop-color="#9a3056"/>
          <stop offset="0.45" stop-color="#b94d74"/>
          <stop offset="1" stop-color="#8c2447"/>
        </linearGradient>
        <radialGradient id="lowerGlow" cx="0.35" cy="0.55" r="0.7">
          <stop offset="0" stop-color="#d46d92" stop-opacity="0.55"/>
          <stop offset="1" stop-color="#6e1a37" stop-opacity="0.25"/>
        </radialGradient>
        <linearGradient id="upperFill" x1="0" y1="0" x2="1" y2="0">
          <stop offset="0" stop-color="#ececee"/>
          <stop offset="0.5" stop-color="#ffffff"/>
          <stop offset="1" stop-color="#ececee"/>
        </linearGradient>
        <radialGradient id="upperShade" cx="0.15" cy="0.35" r="0.6">
          <stop offset="0" stop-color="#ddd7da" stop-opacity="0.8"/>
          <stop offset="1" stop-color="#ffffff" stop-opacity="0"/>
        </radialGradient>
        <radialGradient id="upperShadeRight" cx="0.9" cy="0.75" r="0.45">
          <stop offset="0" stop-color="#ddd7da" stop-opacity="0.7"/>
          <stop offset="1" stop-color="#ffffff" stop-opacity="0"/>
        </radialGradient>
        <linearGradient id="bandFill" x1="0" y1="0" x2="0" y2="1">
          <stop offset="0" stop-color="#3a131f"/>
          <stop offset="1" stop-color="#1f0a11"/>
        </linearGradient>
      </defs>

      <g class="lower-panel" role="img" aria-label="Maroon hexagon pattern">
        <rect x="0" y="440" width="452" height="720" fill="url(#lowerFill)"/>
        <rect x="0" y="440" width="452" height="720" fill="url(#lowerGlow)"/>
      </g>

      <path class="chevron-band" aria-hidden="true" d="M0 455 L226 540 L452 455 L452 535 L226 600 L0 535 Z" fill="url(#bandFill)"/>

      <g class="upper-panel" role="img" aria-label="Faint gear pattern behind the title">
        <path d="M0 0 H452 V460 L226 545 L0 460 Z" fill="url(#upperFill)"/>
        <path d="M0 0 H452 V460 L226 545 L0 460 Z" fill="url(#upperShade)"/>
        <path d="M0 0 H452 V460 L226 545 L0 460 Z" fill="url(#upperShadeRight)"/>
      </g>

      <path class="chevron-edge" aria-hidden="true" d="M0 460 L226 545 L452 460" fill="none" stroke="var(--band-edge)" stroke-width="6"/>
    </svg>

    <header class="brand">
      <span class="brand__dot"></span>
      <span class="brand__name">Norvane Tools</span>
    </header>

    <h1 class="product-title">Machining<br>Lubricant</h1>

    <ul class="features">
      <li class="feature feature--grade">
        <svg class="feature__icon" viewBox="0 0 40 40" aria-hidden="true">
          <circle cx="20" cy="20" r="15" fill="none" stroke="#fff" stroke-width="2.5"/>
        </svg>
        <span>Professional Grade</span>
      </li>
      <li class="feature feature--thick">
        <svg class="feature__icon" viewBox="0 0 40 40" aria-hidden="true" fill="none" stroke="#fff" stroke-width="2">
          <line x1="4" y1="20" x2="36" y2="20"/>
          <line x1="20" y1="2" x2="20" y2="15"/>
          <path d="M15 10 L20 15 L25 10"/>
          <line x1="20" y1="38" x2="20" y2="25"/>
          <path d="M15 30 L20 25 L25 30"/>
        </svg>
        <span>Thick Formula</span>
      </li>
      <li class="feature feature--life">
        <svg class="feature__icon" viewBox="0 0 40 40" aria-hidden="true">
          <circle cx="20" cy="20" r="15" fill="none" stroke="#fff" stroke-width="2.5"/>
        </svg>
        <span class="feature__stack">
          <span class="lead">Dramatically</span>
          <span class="big">Increases</span>
          <span class="tail">Tool Life</span>
        </span>
      </li>
    </ul>

    <div class="feature-rule rule-one"></div>
    <div class="feature-rule rule-two"></div>

    <p class="net-content">Net Wt.<br>16 fl oz.<br>473 ml</p>

    <svg class="guarantee-seal" viewBox="0 0 196 196" role="img" aria-label="Satisfaction guarantee seal">
      <circle cx="98" cy="98" r="96" fill="var(--seal-rim)"/>
      <circle cx="98" cy="98" r="90" fill="var(--seal-silver)"/>
      <circle cx="98" cy="98" r="62" fill="var(--seal-rim)"/>
      <circle cx="98" cy="98" r="57" fill="var(--maroon)"/>
    </svg>
  </main>
</body>
</html>
```